Business Card Design for RB Wine:

I'm looking for a card that has the following.
Front:
- Merlot Colored
- stripe down the middle in silver or gold flake
- RB in block like thick letters with gold or silver flake above stripe
-Wine: below stripe
- a grape bunch that is at the end of the stripe that is made so it can be printed as embossed
Back:
- line down the middle of card in Merlot, card is white background
- to the left Marisa Dutton, (next line) Owner, (next line) Certified Sommelier, GVA
- to the right (listed) restaurant consulting, wine tours, personal tastings, event planning, personal wine buying
- add embossed grape bunch
Also, looking for a piece that slides over like a envelope for a room key for a hotel that says "We met @ PALVIN" and possibly a file for that, that I can edit.
Would like card to be printed on a thicker cardstock

```html
<!DOCTYPE html>
<html lang="en">
<head>
<meta charset="utf-8">
<title>RB Wine – Business Card</title>
<link rel="stylesheet" href="https://fonts.googleapis.com/css2?family=Source+Sans+3:wght@400;600;700&display=swap">
<style>
  :root {
    --backdrop: #000000;
    --merlot: #37041a;
    --merlot-deep: #2c0314;
    --merlot-line: #3a0519;
    --gold: #d4ad3c;
    --gold-light: #e6c66a;
    --gold-dark: #b8902c;
    --card-white: #f3f3f3;
    --ink: #3a0519;
    --ink-soft: #444444;
    --wine-label: #d9d2d4;
  }
  html, body {
    margin: 0;
    padding: 0;
    width: 1200px;
    height: 900px;
    overflow: hidden;
    background: var(--backdrop);
    font-family: "Source Sans 3", "Myriad Pro", Arial, sans-serif;
  }
  .canvas {
    position: relative;
    width: 1200px;
    height: 900px;
  }
  .card {
    position: absolute;
    top: 306px;
    width: 439px;
    height: 271px;
    border-radius: 11px;
    overflow: hidden;
  }
  /* Front */
  .card-front {
    left: 149px;
    background: var(--merlot);
  }
  .brand-name {
    position: absolute;
    left: 146px;
    top: 46px;
    margin: 0;
    font-weight: 700;
    font-size: 104px;
    line-height: 1;
    letter-spacing: -2px;
    color: var(--gold);
  }
  .gold-stripe {
    position: absolute;
    left: 0;
    top: 153px;
    width: 301px;
    height: 15px;
    background: linear-gradient(180deg, var(--gold-light) 0%, var(--gold) 50%, var(--gold-dark) 100%);
  }
  .brand-tagline {
    position: absolute;
    left: 178px;
    top: 176px;
    margin: 0;
    font-size: 14px;
    font-weight: 400;
    letter-spacing: 10px;
    color: var(--wine-label);
  }
  .grape-emboss {
    position: absolute;
    border-radius: 40% 40% 50% 50%;
  }
  .card-front .grape-emboss {
    left: 311px;
    top: 72px;
    width: 100px;
    height: 162px;
    background: radial-gradient(ellipse at 50% 45%, #4a0a25 0%, var(--merlot-deep) 75%);
  }
  /* Back */
  .card-back {
    left: 608px;
    background: var(--card-white);
  }
  .divider {
    position: absolute;
    left: 192px;
    top: 0;
    width: 2px;
    height: 100%;
    background: var(--merlot-line);
  }
  .contact {
    position: absolute;
    left: 32px;
    top: 102px;
    margin: 0;
  }
  .contact-name {
    margin: 0;
    font-size: 16px;
    font-weight: 600;
    color: var(--ink);
    letter-spacing: 0.2px;
  }
  .contact-role,
  .contact-cert {
    margin: 0;
    font-size: 12.5px;
    color: var(--ink-soft);
  }
  .contact-role { margin-top: 5px; }
  .contact-cert { margin-top: 8px; }
  .services {
    position: absolute;
    left: 212px;
    top: 96px;
    margin: 0;
    padding: 0;
    list-style: none;
  }
  .services li {
    position: relative;
    padding-left: 15px;
    font-size: 12.5px;
    line-height: 16px;
    color: #2a2a2a;
  }
  .services li::before {
    content: "";
    position: absolute;
    left: 0;
    top: 5px;
    width: 6px;
    height: 6px;
    border-radius: 50%;
    background: var(--merlot-line);
  }
  .card-back .grape-emboss {
    left: 344px;
    top: 139px;
    width: 68px;
    height: 108px;
    background: radial-gradient(ellipse at 50% 45%, #ffffff 0%, #dcdcdc 80%);
  }
</style>
</head>
<body>
<main class="canvas">
  <section class="card card-front" aria-label="Card front">
    <h1 class="brand-name">RB</h1>
    <div class="gold-stripe"></div>
    <p class="brand-tagline">WINE</p>
    <div class="grape-emboss" role="img" aria-label="Embossed grape bunch illustration"></div>
  </section>

  <section class="card card-back" aria-label="Card back">
    <div class="contact">
      <p class="contact-name">MARISA DUTTON</p>
      <p class="contact-role">Owner</p>
      <p class="contact-cert">Certified Sommelier, GVA</p>
    </div>
    <div class="divider"></div>
    <ul class="services">
      <li>Restaurant Consulting</li>
      <li>Wine Tours</li>
      <li>Personal Tastings</li>
      <li>Event Planning</li>
      <li>Personal wine buying</li>
    </ul>
    <div class="grape-emboss" role="img" aria-label="Embossed grape bunch illustration"></div>
  </section>
</main>
</body>
</html>
```